Floor Inspections and Consulting

We provide inspections and consulting services on various floor coverings, e.g. carpet, hardwood, etc. We also do expert witness work for attorneys due to floor covering failures. We current have a logo, just need it incorporated into a new design. I have examples of cards I have found on the internet that capture my attention and make a statement. I have included our original business card, which in my opinion is terrible, but it does have our logo on it.

```html
<!DOCTYPE html>
<html lang="en">
<head>
<meta charset="utf-8">
<title>Truegrade Floor Inspections – Business Card</title>
<link rel="stylesheet" href="https://fonts.googleapis.com/css2?family=Montserrat:wght@500;700;800;900&display=swap">
<style>
  :root {
    --ink: #121212;
    --orange: #e46f05;
    --orange-deep: #b95803;
    --white: #ffffff;
    --backdrop: #d9d9d9;
  }
  * { margin: 0; padding: 0; box-sizing: border-box; }
  html, body { width: 1200px; height: 1015px; overflow: hidden; }
  body {
    background: var(--backdrop);
    font-family: "Montserrat", Arial, sans-serif;
    position: relative;
  }
  .card {
    position: absolute;
    left: 215px;
    width: 770px;
    height: 440px;
    background: var(--ink);
    overflow: hidden;
    box-shadow: 0 8px 24px rgba(0,0,0,.25);
  }
  .card--front { top: 45px; }
  .card--back  { top: 530px; }

  .brand {
    position: absolute;
    display: flex;
    align-items: center;
    gap: 14px;
    color: var(--orange);
    font-weight: 800;
    text-transform: uppercase;
    line-height: 1.05;
  }
  .brand__mark { width: 22px; height: 22px; background: var(--orange); flex: none; }
  .brand__name { font-size: 30px; letter-spacing: .5px; }

  .card--front .brand { left: 0; right: 0; top: 118px; justify-content: center; }

  .tagline-band {
    position: absolute;
    left: 0; right: 0;
    top: 282px; height: 66px;
    background: var(--orange);
    display: flex; align-items: center; justify-content: center;
  }
  .tagline {
    color: var(--white);
    font-weight: 800;
    font-size: 24px;
    letter-spacing: .3px;
  }

  .card--back .panel { position: absolute; inset: 0; }
  .card--back .brand { left: 500px; top: 160px; }
  .card--back .brand__name { font-size: 25px; }

  .contact {
    position: absolute;
    left: 52px; top: 110px;
    list-style: none;
    color: var(--white);
    font-weight: 500;
    font-size: 21px;
  }
  .contact li { display: flex; align-items: center; gap: 14px; margin-bottom: 16px; }
  .contact svg { width: 24px; height: 24px; flex: none; }
  .person {
    position: absolute;
    left: 52px; top: 278px;
    color: var(--white);
    font-weight: 900;
    font-size: 32px;
    text-transform: uppercase;
    letter-spacing: .3px;
  }
</style>
</head>
<body>

  <section class="card card--front" aria-label="Card front">
    <div class="brand">
      <span class="brand__mark"></span>
      <span class="brand__name">Truegrade Floor<br>Inspections</span>
    </div>
    <div class="tagline-band">
      <p class="tagline">Certified Floor Covering Inspection &amp; Consulting</p>
    </div>
  </section>

  <section class="card card--back" aria-label="Card back">
    <svg class="panel" viewBox="0 0 770 440" preserveAspectRatio="none" aria-hidden="true">
      <polygon points="0,0 392,0 492,440 0,440" fill="var(--orange-deep)"/>
      <polygon points="0,0 378,0 478,440 0,440" fill="var(--orange)"/>
    </svg>

    <ul class="contact">
      <li>
        <svg viewBox="0 0 24 24" fill="none" stroke="#fff" stroke-width="1.8"><rect x="2" y="2" width="20" height="20" rx="2"/><path d="M8 6c-1 1-1 3 1 6s4 5 6 5l1.5-1.5-2.5-2-1.2 1c-1.2-.6-2.4-1.8-3-3l1-1.2-2-2.5z" fill="#fff" stroke="none"/></svg>
        <span>303-555-0148</span>
      </li>
      <li>
        <svg viewBox="0 0 24 24" fill="none" stroke="#fff" stroke-width="1.8"><rect x="2" y="5" width="20" height="14"/><path d="M2 5l10 8 10-8"/></svg>
        <span>dale@truegradefloors.com</span>
      </li>
      <li>
        <svg viewBox="0 0 24 24" fill="none" stroke="#fff" stroke-width="1.8"><circle cx="12" cy="12" r="10"/><ellipse cx="12" cy="12" rx="4.5" ry="10"/><path d="M2 12h20M4 7h16M4 17h16"/></svg>
        <span>www.truegradefloors.com</span>
      </li>
    </ul>

    <p class="person">Dale Morrow</p>

    <div class="brand">
      <span class="brand__mark"></span>
      <span class="brand__name">Truegrade Floor<br>Inspections</span>
    </div>
  </section>

</body>
</html>
```